Web Design Project

We need web design for a new baby products (nursery furniture) business in Australia.

The logo is already done, and I would like to reflect a similar theme throughout the website:
* Clean, white background.
* Use of lime green, purple and orange.
* Similar font to logo for headings
* FUNKY, FASHIONABLE, QUALITY feeling of website.

The main concept is to be attractive to discerning mums who are buying big items like a cot or chest of drawers. These are expensive items and will be considered the most important purchases for a newborn, so the website has to be enticing!!!
Updates

Hello,

Thank you for your submissions. I have received a few questions regarding the font and the coding of this website.

The job I am seeking is for design for an E-commerce store. The font was done by another pixel forge designer, so I do not know what type of font I am sorry.

I was hoping to have more designs by now, so please send them soon, this project is guaranteed!

I also ask you to read the brief properly please. The name of the business is Cradle Corner, as the logo says. The use of design that I have mentioned has only been demonstrated in a couple of designs submitted to me.

I look forward to seeing your work soon!

Kind Regards
Marla

Target Market(s)

Young mothers aged 25-45

Industry/Entity Type

Business

Requirements
Must have
• Must be funky, bright, energetic, attractive visually.
Nice to have
• I like the idea of some floral / design work in faded lime green, purple on some of the edges of different pages. Maybe islamic design? But has to be very fashionable.
Should not have
• Should not have any traditional ideas of baby websites.

ie- no stork, nappy images, teddybears etc.

```html
<!DOCTYPE html>
<html lang="en">
<head>
<meta charset="utf-8">
<title>Cradle Corner – Home</title>
<link rel="stylesheet" href="https://fonts.googleapis.com/css2?family=Cambo&family=Noticia+Text:wght@400;700&family=Arimo:wght@400;700&display=swap">
<style>
  :root {
    --purple-deep: #2a1a78;
    --purple-mid: #3a2a9a;
    --purple: #a36ee0;
    --lime: #8cff00;
    --lime-text: #9be83a;
    --orange: #f58b1e;
    --orange-soft: #f6a34c;
    --yellow: #ffc000;
    --gray-text: #8a8f96;
    --white: #ffffff;
    --heading: "Noticia Text", "Cambo", serif;
    --body: "Arimo", Arial, sans-serif;
  }
  * { box-sizing: border-box; margin: 0; padding: 0; }
  html, body { width: 1000px; height: 1200px; overflow: hidden; background: var(--white); }
  body { position: relative; font-family: var(--body); }
  .masthead {
    position: absolute; left: 0; top: 0; width: 1000px; height: 518px;
    background:
      radial-gradient(ellipse 190px 300px at -20px 270px, rgba(245,139,30,0.95), rgba(245,139,30,0) 100%),
      linear-gradient(160deg, #34207a 0%, #2b2a9c 45%, #251a6e 100%);
  }
  .brand { position: absolute; left: 68px; top: 22px; display: flex; align-items: center; gap: 12px; }
  .brand-dot { width: 58px; height: 58px; border-radius: 50%; background: var(--lime); }
  .brand-name { font-family: var(--heading); font-weight: 700; font-size: 40px; color: var(--lime); line-height: 1; }
  .cart { position: absolute; left: 812px; top: 57px; display: flex; align-items: center; gap: 8px; color: var(--white); font-weight: 700; font-size: 14px; }
  .search { position: absolute; left: 715px; top: 86px; width: 218px; height: 28px; background: var(--white); border: 2px solid #cfd3e6; font-size: 12px; color: #333; padding: 5px 6px; }
  .nav { position: absolute; left: 67px; top: 115px; height: 51px; }
  .nav-tab { position: absolute; bottom: 0; height: 44px; width: 107px; border-radius: 6px 6px 0 0; font-family: var(--heading); font-size: 13px; color: var(--white); text-align: center; line-height: 44px; }
  .nav-tab.home { height: 51px; width: 108px; font-size: 18px; font-weight: 700; line-height: 56px; background: linear-gradient(#f9a552, var(--orange)); }
  .t-lime { background: var(--lime); } .t-purple { background: var(--purple); }
  .t-yellow { background: var(--yellow); } .t-orange { background: var(--orange); }
  .hero { position: absolute; left: 66px; top: 166px; width: 867px; height: 417px;
    background: linear-gradient(180deg, #efe4dc 0%, #f3ece8 55%, #d4772c 62%, #c9671f 100%);
    box-shadow: 0 14px 14px -10px rgba(0,0,0,0.25); }
  .hero-dots { position: absolute; right: 8px; bottom: 20px; display: flex; gap: 4px; }
  .hero-dots span { width: 35px; height: 35px; border-radius: 50%; background: var(--white); }
  .hero-dots span.small { width: 22px; height: 22px; margin-top: 7px; background: #fbe4d4; }
  .promo { position: absolute; left: 68px; width: 262px; height: 131px; border-radius: 9px; overflow: hidden; color: var(--white); }
  .promo svg { position: absolute; inset: 0; }
  .promo h3 { position: absolute; left: 14px; top: 8px; font-family: var(--heading); font-weight: 400; font-size: 18px; }
  .promo p { position: absolute; left: 15px; top: 40px; width: 150px; font-size: 11.5px; font-weight: 700; line-height: 14px; }
  .welcome-title, .gallery-title { position: absolute; left: 437px; font-family: var(--heading); font-weight: 700; font-size: 17px; color: var(--lime-text); }
  .welcome-title { top: 633px; } .gallery-title { top: 872px; }
  .welcome-text { position: absolute; left: 437px; top: 666px; width: 494px; font-size: 11.8px; line-height: 17.6px; color: var(--gray-text); word-break: break-all; }
  .view-more { position: absolute; left: 872px; top: 794px; font-size: 12px; color: var(--lime-text); text-decoration: underline; }
  .divider { position: absolute; left: 440px; top: 835px; width: 488px; height: 1px; background: linear-gradient(90deg, transparent, #8a8f96 30%, #8a8f96 70%, transparent); }
  .arrow { position: absolute; top: 967px; width: 13px; height: 17px; background: #e4e6e8; }
  .product { position: absolute; top: 915px; width: 176px; height: 124px; border-radius: 4px; }
  .product.a { left: 474px; background: linear-gradient(180deg, #f6f6fa 0%, #eeeef4 60%, #e99ad0 85%, #f4f4f8 100%); }
  .product.b { left: 718px; background: linear-gradient(180deg, #f3f3f3 0%, #e9ece8 60%, #f4f4f4 100%); }
  .gallery-split { position: absolute; left: 681px; top: 907px; width: 1px; height: 147px; background: #b9bcc0; }
  .price { position: absolute; top: 1049px; font-size: 12px; font-weight: 700; color: var(--gray-text); text-decoration: underline; }
  .buy { position: absolute; top: 1045px; width: 50px; height: 18px; background: var(--lime); color: #2a2a2a; font-size: 11px; text-align: center; line-height: 18px; }
  .footer { position: absolute; left: 0; top: 1110px; width: 1000px; height: 90px; background: var(--lime); color: var(--white); font-size: 12.5px; }
  .footer-links { position: absolute; left: 68px; top: 25px; }
  .footer-copy { position: absolute; left: 69px; top: 60px; }
  .find-us { position: absolute; left: 835px; top: 26px; font-size: 14px; }
  .social { position: absolute; top: 53px; width: 32px; height: 32px; border-radius: 3px; }
</style>
</head>
<body>
  <header class="masthead">
    <div class="brand"><span class="brand-dot"></span><span class="brand-name">Cradle Corner</span></div>
    <div class="cart">Add to cart :
      <svg width="30" height="26" viewBox="0 0 30 26"><path d="M1 3h5l4 14h14l4-10H8" fill="none" stroke="#8cff00" stroke-width="2.5" stroke-linejoin="round"/><circle cx="12" cy="22" r="2.4" fill="#8cff00"/><circle cx="22" cy="22" r="2.4" fill="#8cff00"/></svg>
    </div>
    <div class="search">Search here:</div>
    <nav class="nav">
      <div class="nav-tab home" style="left:0">Home</div>
      <div class="nav-tab t-lime" style="left:110px">Baby furniture</div>
      <div class="nav-tab t-purple" style="left:219px">Manufacturing</div>
      <div class="nav-tab t-yellow" style="left:329px">Baby cots</div>
      <div class="nav-tab t-orange" style="left:438px">Our service</div>
      <div class="nav-tab t-lime" style="left:548px">About us</div>
      <div class="nav-tab t-yellow" style="left:657px">Contact us</div>
    </nav>
  </header>

  <div class="hero" role="img" aria-label="Photo of a white nursery room with cot, chest of drawers, wardrobe and toy box on a timber floor">
    <div class="hero-dots"><span class="small"></span><span></span><span></span><span></span></div>
  </div>

  <section class="promo" style="top:625px">
    <svg width="262" height="131" viewBox="0 0 262 131"><rect width="262" height="131" fill="#8cff00"/><path d="M160 131 C170 70 210 35 262 28 V131Z" fill="#f2eee8" role="img" aria-label="Photo of a white nursery furniture set"/></svg>
    <h3>Baby Furniture</h3>
    <p>Lorem ipsum dolor sit amet, adipiscing elit. Ut comus imperdiet urna justo mperdiet ....</p>
  </section>
  <section class="promo" style="top:775px">
    <svg width="262" height="131" viewBox="0 0 262 131"><rect width="262" height="131" fill="#a36ee0"/><path d="M135 131 C150 70 200 35 262 28 V131Z" fill="#5a4030" role="img" aria-label="Photo of hands crafting a timber furniture part"/></svg>
    <h3>Manufactured</h3>
    <p>Lorem ipsum dolor sit amet, adipiscing elit. Ut comus imperdiet urna justo mperdiet ....</p>
  </section>
  <section class="promo" style="top:928px">
    <svg width="262" height="131" viewBox="0 0 262 131"><rect width="262" height="131" fill="#ffc800"/><path d="M150 131 C160 70 205 35 262 28 V131Z" fill="#e8dccb" role="img" aria-label="Photo of a timber baby cot"/></svg>
    <h3>Baby Cots</h3>
    <p>Lorem ipsum dolor sit amet, adipiscing elit. Ut comus imperdiet urna justo mperdiet ....</p>
  </section>

  <h2 class="welcome-title">Welcome to our site......</h2>
  <p class="welcome-text">Lorem ipsum dolor sit amet, consectetur adipiscing elit. Cras laoreet sollicitudin sem, ut sollicitudin magna placerat ultrices. In suscipit lectus non tellus porttitor ullamcorper. Vestibulum viverra, sapien quis euismod bibendum, dui nisi accumsan dui, tincidunt tempor tellus ante eu metus. Aliquam eget nisl nibh, a laoreet urna. Nullam neque turpis, convallis id tempus at, varius vitae felis. Suspendisse convallis risus quis ipsum consequat volutpat. Etiam non laoreet nisi. Vestibulum imperdiet bibendum mauris. Morbi eu ipsum justo. Vestibulum iaculis sollicitudin purus vitae fauci a laoreet urna. Nullam neque turpis..........</p>
  <span class="view-more">View more</span>
  <div class="divider"></div>

  <h2 class="gallery-title">Our Gallery.......</h2>
  <div class="arrow" style="left:437px"><svg width="13" height="17"><path d="M8 5 L4 8.5 L8 12Z" fill="#fff"/></svg></div>
  <div class="arrow" style="left:920px"><svg width="13" height="17"><path d="M5 5 L9 8.5 L5 12Z" fill="#fff"/></svg></div>
  <div class="product a" role="img" aria-label="Product photo of a white toddler bed with pink bedding"></div>
  <div class="gallery-split"></div>
  <div class="product b" role="img" aria-label="Product photo of a white baby cot"></div>
  <span class="price" style="left:476px">$:1400</span>
  <span class="buy" style="left:594px">Buy now</span>
  <span class="price" style="left:719px">$:1800</span>
  <span class="buy" style="left:844px">Buy now</span>

  <footer class="footer">
    <div class="footer-links">Home &nbsp;|&nbsp; Baby FurnitureBaby Clothes &nbsp;|&nbsp; Babay Cots &nbsp;|&nbsp; Our Service &nbsp;|&nbsp; About us &nbsp;|&nbsp; Contact us</div>
    <div class="footer-copy">Cradle Corner © 2012 | Privicy policy</div>
    <div class="find-us">Find us on :</div>
    <span class="social" style="left:819px;background:#3355a8"></span>
    <span class="social" style="left:859px;background:#d8282e"></span>
    <span class="social" style="left:899px;background:#2a8fd0"></span>
  </footer>
</body>
</html>
```